High Tech Real Estate Startup needs a business card

We are developing an innovative real estate marketing product based around advanced search and virtual reality.

We talk to people, we need business cards.

Target Market(s)

The target market is technology professionals and realtors.

Contact Information for Business Card

The information to be included will include

Name
Title
Phone Number
E-mail Address
www.zelquin.com

It should use simple iconography for each one of those fields.

Font styles to use
Other font styles liked:
• Co, Jubilat, Avenir

Colors

Designer to choose colors to be used in the design.

Requirements
Must have
• Clean aesthetic,
• Good use of negative space.
• It should use our company logo, shown in the attached file. It is able to use the negative of that logo (coloured font and white background) and I have attached other acceptable accent colours in a swatch file.
Should not have
• Should not be too busy
• No extraneous text (slogans, tag lines etc)

```html
<!DOCTYPE html>
<html lang="en">
<head>
<meta charset="utf-8">
<title>Zelquin Business Card</title>
<link rel="stylesheet" href="https://fonts.googleapis.com/css2?family=Roboto:wght@400;500&family=Roboto+Condensed:wght@500&display=swap">
<style>
  :root {
    --backdrop: #2b2b2b;
    --card-teal: #04bbbe;
    --ink-white: #ffffff;
    --ink-soft: #e3f7f7;
    --divider: rgba(255, 255, 255, 0.55);
  }
  * { margin: 0; padding: 0; box-sizing: border-box; }
  html, body {
    width: 1200px;
    height: 960px;
    overflow: hidden;
    background: var(--backdrop);
  }
  .canvas {
    position: relative;
    width: 1200px;
    height: 960px;
  }
  .card {
    position: absolute;
    left: 320px;
    width: 600px;
    height: 343px;
    background: var(--card-teal);
    color: var(--ink-white);
    font-family: "Roboto", Arial, sans-serif;
  }
  .card--front { top: 107px; }
  .card--back { top: 493px; }

  .wordmark {
    font-family: "Roboto", Arial, sans-serif;
    font-weight: 500;
    color: var(--ink-white);
    letter-spacing: 3px;
    line-height: 1;
    white-space: nowrap;
  }
  .card--front .wordmark {
    position: absolute;
    left: 0;
    right: 0;
    top: 138px;
    text-align: center;
    font-size: 70px;
  }
  .front-url {
    position: absolute;
    left: 0;
    right: 0;
    top: 261px;
    text-align: center;
    font-size: 14px;
    letter-spacing: 4px;
    color: var(--ink-soft);
  }

  .card--back .wordmark {
    position: absolute;
    left: 60px;
    width: 250px;
    top: 152px;
    text-align: center;
    font-size: 44px;
  }
  .divider {
    position: absolute;
    left: 326px;
    top: 110px;
    width: 1px;
    height: 132px;
    background: var(--divider);
  }
  .contact-block {
    position: absolute;
    left: 356px;
    top: 112px;
  }
  .person-name {
    font-family: "Roboto Condensed", Arial, sans-serif;
    font-weight: 500;
    font-size: 23px;
    line-height: 1;
    letter-spacing: 0.2px;
  }
  .person-title {
    margin-top: 6px;
    font-size: 15px;
    line-height: 1;
    color: var(--ink-soft);
  }
  .contact-list {
    list-style: none;
    margin-top: 19px;
  }
  .contact-item {
    display: flex;
    align-items: center;
    height: 19px;
    font-size: 14px;
    color: var(--ink-soft);
  }
  .contact-icon {
    width: 13px;
    height: 13px;
    margin-right: 9px;
    flex: none;
  }
</style>
</head>
<body>
<main class="canvas">
  <section class="card card--front" aria-label="Card front">
    <div class="wordmark">ZELQUIN</div>
    <div class="front-url">WWW.ZELQUIN.COM</div>
  </section>

  <section class="card card--back" aria-label="Card back">
    <div class="wordmark">ZELQUIN</div>
    <div class="divider"></div>
    <div class="contact-block">
      <div class="person-name">DARA VELMONT</div>
      <div class="person-title">CEO/FOUNDER</div>
      <ul class="contact-list">
        <li class="contact-item">
          <svg class="contact-icon" viewBox="0 0 16 16" aria-hidden="true">
            <path fill="#fff" d="M3.6 1.2l2.3 2.6c.3.4.3.9 0 1.3L4.8 6.3c.9 2 2.5 3.6 4.6 4.6l1.2-1.1c.4-.3.9-.3 1.3 0l2.6 2.3c.4.4.4 1 0 1.4l-1.3 1.3C11.6 16.4 0 8.5 1 2.6l1.3-1.4c.4-.4 1-.4 1.3 0z"/>
          </svg>
          555 014 2738
        </li>
        <li class="contact-item">
          <svg class="contact-icon" viewBox="0 0 16 16" aria-hidden="true">
            <rect x="1" y="3" width="14" height="10" fill="#fff"/>
            <path d="M1.5 3.5L8 9l6.5-5.5" fill="none" stroke="#04bbbe" stroke-width="1.4"/>
          </svg>
          dara@zelquin.com
        </li>
        <li class="contact-item">
          <svg class="contact-icon" viewBox="0 0 16 16" aria-hidden="true">
            <circle cx="8" cy="8" r="7" fill="#fff"/>
            <path d="M4 4.5c1.5 0 2 1 3 1.5s.5 2-1 2.5-1 2.5-2 3M10.5 3c0 1.5 1 2 2.5 2M9 13c.5-1.5 1.5-2 3-2.5" fill="none" stroke="#04bbbe" stroke-width="1.3"/>
          </svg>
          www.zelquin.com
        </li>
      </ul>
    </div>
  </section>
</main>
</body>
</html>
```